Coastline Premier Retreats Business Card Design

Design a business card for Coastline Premier Retreats. Look at the website for colors and reference. Card should have logo, name, title, office number, mobile number, email, URL and a tagline like, "Luxury Hotel & Resort Email Marketing" (This might change).

https://www.coastlinepremierretreats.example

The rest I will leave up to your imagination.

Contact Information for Business Card

Logo, name, title, office number, mobile number, email, URL and a tagline like, "Luxury Hotel & Resort Email Marketing" (This might change).

```html
<!DOCTYPE html>
<html lang="en">
<head>
<meta charset="utf-8">
<title>Coastline Premier Retreats – Business Card</title>
<link href="https://fonts.googleapis.com/css2?family=Arimo:wght@400;700&display=swap" rel="stylesheet">
<style>
  :root {
    --bg: #d9d9d9;
    --card-black: #050505;
    --card-orange: #e36c00;
    --accent: #f07c12;
    --white: #ffffff;
    --ink: #111111;
    --rule: #8a8a8a;
  }
  * { margin: 0; padding: 0; box-sizing: border-box; }
  html, body { width: 1200px; height: 800px; overflow: hidden; }
  body {
    background: var(--bg);
    font-family: "Arimo", Arial, sans-serif;
    display: flex;
    align-items: center;
    justify-content: center;
    gap: 40px;
  }
  .card {
    width: 540px;
    height: 310px;
    border-radius: 22px;
    position: relative;
    overflow: hidden;
  }
  /* Front */
  .card-front { background: var(--card-black); color: var(--white); }
  .brand-front {
    position: absolute;
    top: 40px;
    right: 36px;
    font-weight: 700;
    font-size: 22px;
    letter-spacing: 0.5px;
    text-transform: uppercase;
    color: var(--white);
    text-align: right;
    line-height: 1.15;
  }
  .divider {
    position: absolute;
    left: 36px;
    right: 36px;
    top: 198px;
    height: 1px;
    background: var(--rule);
  }
  .person {
    position: absolute;
    left: 36px;
    bottom: 120px;
  }
  .person-name { color: var(--accent); font-weight: 700; font-size: 21px; }
  .person-title { font-size: 14px; margin-top: 3px; }
  .tagline {
    position: absolute;
    right: 36px;
    bottom: 120px;
    font-size: 13px;
  }
  .contact-list { position: absolute; top: 212px; list-style: none; font-size: 13px; }
  .contact-list li { display: flex; align-items: center; gap: 8px; height: 21px; }
  .contact-phones { left: 36px; }
  .contact-web { right: 36px; }
  .contact-web li { justify-content: flex-end; }
  .icon { width: 12px; height: 12px; flex: none; }
  /* Back */
  .card-back { background: var(--card-orange); }
  .brand-back {
    position: absolute;
    top: 92px;
    left: 0; right: 0;
    text-align: center;
    font-weight: 700;
    font-size: 34px;
    text-transform: uppercase;
    color: var(--ink);
    line-height: 1.1;
  }
  .url-back {
    position: absolute;
    top: 222px;
    left: 0; right: 0;
    text-align: center;
    color: var(--white);
    font-size: 13px;
    letter-spacing: 2.4px;
  }
</style>
</head>
<body>
  <section class="card card-front" aria-label="Business card front">
    <div class="brand-front">Coastline Premier<br>Retreats</div>

    <div class="person">
      <div class="person-name">Daniel Brooks</div>
      <div class="person-title">President</div>
    </div>
    <div class="tagline">Luxury Hotel &amp; Resort Email Marketing</div>

    <div class="divider"></div>

    <ul class="contact-list contact-phones">
      <li>
        <svg class="icon" viewBox="0 0 12 12" aria-hidden="true"><path d="M3 1 L5 3.5 L4 5 Q5.5 7 7 8 L8.5 7 L11 9 L9.5 11 Q4 10 1 2.5 Z" fill="var(--accent)"/></svg>
        555.240.3100
      </li>
      <li>
        <svg class="icon" viewBox="0 0 12 12" aria-hidden="true"><rect x="2.5" y="0.8" width="7" height="10.4" rx="1" fill="none" stroke="var(--accent)" stroke-width="1.4"/></svg>
        555.240.3101
      </li>
    </ul>

    <ul class="contact-list contact-web">
      <li>
        info@coastlinepremierretreats.example
        <svg class="icon" viewBox="0 0 12 12" aria-hidden="true"><rect x="0.5" y="2" width="11" height="8" fill="var(--accent)"/><path d="M0.5 2 L6 6.5 L11.5 2" fill="none" stroke="var(--card-black)" stroke-width="1"/></svg>
      </li>
      <li>
        www.coastlinepremierretreats.example
        <svg class="icon" viewBox="0 0 12 12" aria-hidden="true"><circle cx="6" cy="6" r="5.5" fill="var(--accent)"/><path d="M0.5 6 H11.5 M6 0.5 Q2.5 6 6 11.5 M6 0.5 Q9.5 6 6 11.5" fill="none" stroke="var(--card-black)" stroke-width="0.9"/></svg>
      </li>
    </ul>
  </section>

  <section class="card card-back" aria-label="Business card back">
    <div class="brand-back">Coastline Premier<br>Retreats</div>
    <div class="url-back">www.coastlinepremierretreats.example</div>
  </section>
</body>
</html>
```